professional business card design

Business card design. Photos have been uploaded and i am open to the designer choosing which photos to use. Would like the card to be mostyly in a grey scale design with black, whites, silver & grey colours. I have added copy of our flyer as would like on the back side of card our services to be listed. Do not use any bright colurs such as blue red green or yellow. i need to be able to edit the phone number and naem in the final card design submitted.

Target Market(s)

Clients

Industry/Entity Type

earhmovibng and transport

Contact Information for Business Card

Director Name, address, email, phone number and services

Colors

Designer to choose only greyscale colors for use in the design.

Requirements
Should not have
• no yellow, red, blue or green

```html
<!DOCTYPE html>
<html lang="en">
<head>
<meta charset="utf-8">
<title>Dunmore Road Haulage – Business Card</title>
<link rel="stylesheet" href="https://fonts.googleapis.com/css2?family=Exo+2:wght@500;600;700&family=Open+Sans:wght@600;700&display=swap">
<style>
  :root {
    --page: #d9d6d1;
    --black: #0b0b0b;
    --charcoal: #222;
    --white: #ffffff;
    --silver-light: #f4f4f4;
    --silver: #c9c9c9;
    --silver-dark: #8a8a8a;
    --ink: #111;
  }
  * { margin: 0; padding: 0; box-sizing: border-box; }
  html, body { width: 900px; height: 1200px; overflow: hidden; }
  body { background: var(--page); position: relative; font-family: "Open Sans", sans-serif; }

  .card {
    position: absolute; left: 78px; width: 744px; height: 440px;
    border-radius: 28px; overflow: hidden;
    box-shadow: 0 6px 14px rgba(0,0,0,.45);
  }

  /* Front */
  .card-front { top: 132px; background: radial-gradient(ellipse at 50% 40%, #2c2c2c 0%, #141414 55%, var(--black) 100%); }
  .brand-name {
    position: absolute; left: 56px; top: 180px; width: 310px;
    font-family: "Exo 2", sans-serif; font-weight: 700; font-size: 86px;
    letter-spacing: 16px; color: var(--silver); line-height: 1;
  }
  .divider { position: absolute; left: 390px; top: 163px; width: 2px; height: 128px; background: var(--silver-light); }
  .contact { position: absolute; left: 420px; top: 155px; color: var(--white); font-family: "Exo 2", sans-serif; }
  .contact-name { font-size: 25px; font-weight: 700; letter-spacing: .5px; line-height: 1.1; }
  .contact-title { font-size: 16px; font-weight: 600; margin-bottom: 18px; }
  .contact-row { display: flex; align-items: center; gap: 12px; font-size: 16px; font-weight: 500; height: 23px; letter-spacing: .3px; }
  .contact-row svg { width: 14px; height: 14px; fill: var(--white); flex: none; }

  .depot-band {
    position: absolute; left: 0; top: 333px; width: 100%; height: 40px;
    background: linear-gradient(90deg, #ffffff 0%, #f1f1f1 55%, #a9a9a9 100%);
    color: var(--ink); font-family: "Exo 2", sans-serif; font-weight: 700; font-size: 17.5px;
    letter-spacing: 1.1px; display: flex; align-items: center; padding-left: 60px; white-space: nowrap;
  }

  /* Back */
  .card-back { top: 638px; background: radial-gradient(ellipse at 55% 40%, #ffffff 0%, #e4e4e4 35%, #a8a8a8 75%, #8c8c8c 100%); }
  .truck-photo {
    position: absolute; left: 0; top: 8px; width: 390px; height: 404px;
    background: linear-gradient(160deg, #bfc3c6 0%, #9da2a6 45%, #5b5f63 80%, #3a3c3e 100%);
    border-radius: 0 0 0 28px;
  }
  .services-title {
    position: absolute; right: 22px; top: 48px;
    font-family: "Exo 2", sans-serif; font-weight: 700; font-size: 25px; color: var(--ink); letter-spacing: .5px;
  }
  .services-list { position: absolute; right: 19px; top: 91px; list-style: none; text-align: right; }
  .services-list li {
    font-size: 13.5px; font-weight: 700; color: var(--ink); height: 29.3px; line-height: 29.3px;
    display: flex; justify-content: flex-end; align-items: center; gap: 17px; white-space: nowrap;
  }
  .services-list li::after { content: ""; width: 6px; height: 6px; background: var(--ink); flex: none; }
</style>
</head>
<body>
  <section class="card card-front">
    <div class="brand-name">DRH</div>
    <div class="divider"></div>
    <div class="contact">
      <div class="contact-name">PETER HOLLIS</div>
      <div class="contact-title">Director</div>
      <div class="contact-row">
        <svg viewBox="0 0 16 16"><path d="M2 5c0-2 3-3 6-3s6 1 6 3v1h-3V5H5v1H2z"/><rect x="3" y="7" width="10" height="7" rx="1"/></svg>
        <span>000 555 000</span>
      </div>
      <div class="contact-row">
        <svg viewBox="0 0 16 16"><path d="M1 3h14v10H1z M1 3l7 6 7-6" fill="none" stroke="#fff" stroke-width="1.6"/></svg>
        <span>info@dunmorehaulage.com.au</span>
      </div>
      <div class="contact-row">
        <svg viewBox="0 0 16 16"><circle cx="8" cy="8" r="7"/><path d="M3 5h4l1 3-2 2 1 4M10 2l1 3 3 1" fill="none" stroke="#111" stroke-width="1.3"/></svg>
        <span>www.dunmorehaulage.com.au</span>
      </div>
    </div>
    <div class="depot-band">DEPOT : DRH LOT 14, QUARRY CREEK ROAD, STONEBRIDGE, AUSTRALIA</div>
  </section>

  <section class="card card-back">
    <div class="truck-photo" role="img" aria-label="Photo of a white prime mover truck with an oversize sign on the front bumper"></div>
    <h2 class="services-title">OUR SERVICES</h2>
    <ul class="services-list">
      <li>Over size load / Hot Shot Load</li>
      <li>Heavy Vehicle Recovery services</li>
      <li>potable water delivers</li>
      <li>Road Building / Maintenance</li>
      <li>Earthworks</li>
      <li>Send &amp; Metal Supply &amp; cartage</li>
      <li>Road train Trippers</li>
      <li>Road train Tankers</li>
      <li>Road train flat tops</li>
      <li>Drop Deck Trailers</li>
      <li>Mine site accredited equipment &amp; oparetors</li>
    </ul>
  </section>
</body>
</html>
```